Sparrow Haulage needs a business card design.

Design a double-sided business card for new freight business. On the front, would like to see our logo along with the following info:

Martin Obuya
CEO/FOUNDER
555-206-7142
martinobuya@sparrow-haulage.example

On the reverse side, we would like to use the graphic image of our logo only without the Sparrow Haulage name.

```html
<!DOCTYPE html>
<html lang="en">
<head>
<meta charset="utf-8">
<title>Sparrow Haulage — Business Card</title>
<link rel="stylesheet" href="https://fonts.googleapis.com/css2?family=Michroma&family=Nunito+Sans:wght@400;700&display=swap">
<style>
  :root {
    --backdrop: #dcdde0;
    --card-white: #ffffff;
    --navy: #1b1a55;
    --navy-light: #2a2a72;
    --navy-deep: #17164a;
    --red: #bf1e2e;
    --ink: #3a3a3a;
  }
  * { margin: 0; padding: 0; box-sizing: border-box; }
  html, body {
    width: 1200px; height: 859px; overflow: hidden;
    background: var(--backdrop);
    font-family: "Nunito Sans", sans-serif;
  }
  .card {
    position: absolute; left: 319px; width: 562px; height: 321px;
  }
  .card-front { top: 69px; background: var(--card-white); }
  .card-back { top: 470px; background: var(--navy); }

  .brand {
    position: absolute; left: 0; right: 0; top: 108px;
    display: flex; align-items: center; justify-content: center; gap: 12px;
  }
  .brand-mark { width: 22px; height: 22px; background: var(--red); flex: none; }
  .brand-name {
    font-family: "Michroma", sans-serif; font-size: 22px; line-height: 1; letter-spacing: 2px;
    color: var(--navy); text-transform: uppercase; white-space: nowrap;
  }

  .holder {
    position: absolute; right: 303px; top: 220px; text-align: right; white-space: nowrap;
  }
  .holder-name { font-weight: 700; font-size: 19px; line-height: 1; color: var(--navy); }
  .holder-name .surname { color: var(--red); }
  .holder-title { font-size: 12.5px; line-height: 1; color: var(--ink); margin-top: 7px; letter-spacing: .3px; }

  .divider {
    position: absolute; left: 274px; top: 217px; width: 1.5px; height: 45px; background: var(--ink);
  }

  .contact {
    position: absolute; left: 291px; top: 211px; list-style: none;
  }
  .contact li {
    display: flex; align-items: center; gap: 7px;
    font-size: 13px; line-height: 18px; color: var(--ink); white-space: nowrap;
  }
  .contact svg { width: 10px; height: 10px; fill: var(--red); flex: none; }

  .back-mark {
    position: absolute; left: 200px; top: 75px; width: 162px; height: 162px;
    background: linear-gradient(135deg, var(--navy-light), var(--navy-deep));
  }
</style>
</head>
<body>
  <section class="card card-front">
    <div class="brand">
      <span class="brand-mark"></span>
      <span class="brand-name">Sparrow Haulage</span>
    </div>

    <div class="holder">
      <p class="holder-name">Martin <span class="surname">Obuya</span></p>
      <p class="holder-title">CEO/FOUNDER</p>
    </div>

    <span class="divider"></span>

    <ul class="contact">
      <li>
        <svg viewBox="0 0 10 10" aria-hidden="true"><path d="M2 0.5l1.8 2.2-1 1.2c.6 1.3 1.5 2.2 2.8 2.8l1.2-1L9.5 8 8.3 9.5C4.2 9.3.7 5.8.5 1.7z"/></svg>
        555-206-7142
      </li>
      <li>
        <svg viewBox="0 0 10 10" aria-hidden="true"><path d="M0 2h10v6H0z M0.8 2.5L5 5.7 9.2 2.5" stroke="#fff" stroke-width=".8"/></svg>
        martinobuya@sparrow-haulage.example
      </li>
      <li>
        <svg viewBox="0 0 10 10" aria-hidden="true"><circle cx="5" cy="5" r="4.6"/><path d="M3 2.5c1 .5 1 1.5 2 1.8s.6 1.6-.4 2M6.5 6.5c.8 0 1.2.8 1.4 1.5" stroke="#fff" stroke-width=".7" fill="none"/></svg>
        www.sparrow-haulage.example
      </li>
    </ul>
  </section>

  <section class="card card-back">
    <span class="back-mark" aria-hidden="true"></span>
  </section>
</body>
</html>
```